Brand new redesign of Brightpath finance website

I need a new website design that i can advertise a great low interest rate on the front page and capture input application details that will send through to my email address.

some car finance companies will be similar to this would be listed below

tallowcredit.example.com.au
mirabelfinance.example.com.au
finance725.example.com.au
quenbyfinance.example.com.au
finance91.example.com.au

Reason: I have changed the project to a committed project. all the webpages should have the same format just different content and i want to be able to edit the front page easily to update my interest rates.

Target Market(s)

Australian Finance market targeting a younger demographic

Industry/Entity Type

Finance

Coding

Coded - Design and coding required

Number of Pages Required

5+ page

Font styles to use
Serif
Sans Serif

Colors
0255a3
ffffff
cedeed

Requirements
Must have
• application capture form
• apply now buttons
• Headline rate front page

```html
<!DOCTYPE html>
<html lang="en">
<head>
<meta charset="utf-8">
<title>Brightpath Finance – Home</title>
<link href="https://fonts.googleapis.com/css2?family=Roboto:wght@400;500;700&family=Lato:wght@400;700&display=swap" rel="stylesheet">
<style>
:root{
  --blue:#0255a3;
  --white:#ffffff;
  --pale:#cedeed;
  --ink:#2b2b2b;
  --line:#d6d6d6;
  --field:#ffffff;
}
*{box-sizing:border-box;margin:0;padding:0}
html,body{width:793px;height:1200px;overflow:hidden;background:var(--white)}
body{font-family:"Roboto",Arial,sans-serif;color:var(--ink);position:relative}
.abs{position:absolute}

/* top bar */
.topbar{left:0;top:0;width:793px;height:29px;background:var(--blue)}
.social{top:5px;width:20px;height:20px;border-radius:2px}
.social.s1{left:53px;background:#3b5a9a}
.social.s2{left:81px;background:#3aa9e0}
.social.s3{left:109px;background:#c4302b}
.apply{left:549px;top:4px;width:70px;height:21px;background:#e2e2e2;color:#333;font-size:11px;line-height:21px;text-align:center}
.phone-top{left:637px;top:6px;color:var(--white);font-size:14px;font-weight:500;display:flex;align-items:center;gap:5px}

/* nav */
.nav{left:0;top:29px;width:793px;height:81px;border-bottom:1px solid #c8c8c8}
.nav a{position:absolute;top:34px;font-size:11px;color:#333;text-decoration:none;white-space:nowrap}
.nav a.active{color:var(--blue)}
.nav .sep{position:absolute;top:32px;width:1px;height:14px;background:#cfcfcf}
.brand{left:336px;top:4px;width:120px;text-align:center}
.brand .dot{width:44px;height:44px;border-radius:50%;background:var(--blue);margin:0 auto 4px}
.brand .name{font-size:14px;font-weight:700;color:var(--blue);line-height:15px;letter-spacing:.5px}

/* hero */
.hero{left:0;top:110px;width:793px;height:308px;background:linear-gradient(90deg,#eef1f4 0%,#f6f7f8 55%,#e9ecef 100%)}
.hero-photo{left:0;top:0;width:360px;height:308px;background:linear-gradient(90deg,#3a404c 0%,#2b3140 45%,#6b717c 75%,rgba(238,241,244,0) 100%)}
.arrow{top:140px;color:#fff;font-size:28px;font-weight:300}
.perks{left:358px;top:70px;list-style:none}
.perks li{font-size:11.5px;color:var(--blue);margin-bottom:9px;padding-left:14px;position:relative;line-height:15px}
.perks li::before{content:"»";position:absolute;left:0;top:0;font-size:11px}
.stamp{left:428px;top:166px;width:106px;height:106px;border-radius:50%;border:3px solid #9a9a9a;opacity:.7}

.quote{left:552px;top:17px;width:188px;height:252px;background:#dce7f1}
.quote h3{background:var(--blue);color:var(--white);font-size:14px;font-weight:500;height:29px;line-height:29px;padding-left:12px}
.field{position:absolute;left:12px;width:164px;height:22px;background:var(--field);font-family:"Lato",sans-serif;font-size:7.5px;color:#8a8a8a;line-height:22px;padding-left:10px}
.agree{position:absolute;left:12px;top:193px;font-family:"Lato",sans-serif;font-size:7.5px;color:#444;display:flex;align-items:center;gap:8px}
.agree span.box{width:11px;height:11px;background:#fff;border:1px solid #cfcfcf}
.quote .cta{position:absolute;left:8px;top:217px;width:165px;height:27px;background:var(--blue);color:#fff;font-size:12.5px;font-weight:700;text-align:center;line-height:27px}

/* intro */
.h2{font-size:21px;font-weight:400;color:#555;letter-spacing:.2px}
.h2 b{color:var(--blue);font-weight:400}
.rule{height:1px;background:var(--line)}
.rule::after{content:"";position:absolute;left:30px;top:0;border:5px solid transparent;border-top-color:var(--blue)}
.copy{font-family:"Lato",sans-serif;font-size:9.2px;line-height:15px;color:#333}
.call{left:54px;top:617px;font-size:17px;color:#333}
.call b{color:var(--blue);font-weight:700;font-size:23px;margin-left:8px}
.vdiv{left:369px;top:470px;width:1px;height:190px;background:#e4e4e4}
.loan{width:170px}
.loan .ic{position:absolute;left:0;top:0;width:35px;height:35px;border-radius:50%;background:var(--blue);display:flex;align-items:center;justify-content:center}
.loan h4{position:absolute;left:46px;top:4px;font-size:14.5px;font-weight:500;color:#333}
.loan p{position:absolute;left:46px;top:28px;width:130px;font-family:"Lato",sans-serif;font-size:8px;line-height:11.5px;color:#444}

/* bands */
.band-photo{left:0;top:691px;width:793px;height:159px;background:linear-gradient(90deg,#3c3a38 0%,#5a544e 40%,#6e6760 70%,#4d4843 100%)}
.band-photo h2{position:absolute;left:55px;top:50px;font-size:30px;font-weight:400;color:#fff;letter-spacing:.3px}
.band-photo p{position:absolute;left:55px;top:93px;font-size:15px;color:#fff}
.btn-blue{position:absolute;left:582px;top:62px;width:147px;height:35px;background:var(--blue);color:#fff;font-size:16.5px;font-weight:500;text-align:center;line-height:35px}
.band-blue{left:0;top:850px;width:793px;height:158px;background:var(--blue)}
.band-blue h2{position:absolute;left:54px;top:44px;font-size:23px;font-weight:400;color:#fff}
.band-blue p{position:absolute;left:55px;top:79px;font-size:15px;color:#fff}
.btn-light{position:absolute;left:593px;top:56px;width:134px;height:35px;background:#e9ecef;color:#333;font-size:16.5px;font-weight:500;text-align:center;line-height:35px}

/* footer */
.footer{left:0;top:1008px;width:793px;height:192px;background:var(--pale)}
.foot-brand{left:52px;top:30px;width:140px;text-align:center}
.foot-brand .dot{width:72px;height:72px;border-radius:50%;background:#9ea4aa;margin:0 auto 8px}
.foot-brand .name{font-size:10px;font-weight:700;color:#8d939a;letter-spacing:.4px;white-space:nowrap}
.foot-phone{left:52px;top:142px;width:140px;text-align:center;font-size:17px;font-weight:500;color:var(--blue)}
.foot-div{left:209px;top:28px;width:1px;height:150px;border-left:1px dashed #b5c3d1}
.foot-links{left:243px;top:44px;font-size:12px;color:#333;word-spacing:1px;white-space:pre}
.contact{top:80px;display:flex;gap:10px;align-items:flex-start}
.contact .ic{width:35px;height:35px;border-radius:50%;background:var(--blue);display:flex;align-items:center;justify-content:center;flex:none}
.contact .txt{font-size:10.5px;line-height:14px;color:#333;white-space:nowrap}
.cdiv{top:76px;width:1px;height:50px;background:#b5c3d1}
.foot-rule{left:276px;top:135px;width:440px;border-top:1px dashed #b5c3d1}
.copyright{left:370px;top:152px;font-family:"Lato",sans-serif;font-size:8.8px;color:#333}
.base{left:0;top:1197px;width:793px;height:3px;background:var(--blue)}
</style>
</head>
<body>

<header>
  <div class="abs topbar">
    <span class="abs social s1"></span>
    <span class="abs social s2"></span>
    <span class="abs social s3"></span>
    <div class="abs apply">APPLY NOW</div>
    <div class="abs phone-top">
      <svg width="11" height="11" viewBox="0 0 24 24"><path fill="#fff" d="M6.6 10.8a15 15 0 0 0 6.6 6.6l2.2-2.2c.3-.3.7-.4 1-.2 1.1.4 2.3.6 3.6.6.6 0 1 .4 1 1V20c0 .6-.4 1-1 1A17 17 0 0 1 3 4c0-.6.4-1 1-1h3.5c.6 0 1 .4 1 1 0 1.3.2 2.5.6 3.6.1.3 0 .7-.2 1z"/></svg>
      555-018-2473
    </div>
  </div>

  <nav class="abs nav">
    <a class="active" style="left:71px">HOME</a>
    <span class="sep" style="left:126px"></span>
    <a style="left:152px">ABOUT US</a>
    <span class="sep" style="left:227px"></span>
    <a style="left:252px">LOANS &#8964;</a>
    <div class="abs brand">
      <div class="dot"></div>
      <div class="name">BRIGHTPATH<br>FINANCE</div>
    </div>
    <a style="left:466px">INSURANCE</a>
    <span class="sep" style="left:532px"></span>
    <a style="left:541px;letter-spacing:-.2px">FINANCE CALCULATOR</a>
    <span class="sep" style="left:664px"></span>
    <a style="left:673px">CONTACT US</a>
  </nav>
</header>

<section class="abs hero">
  <div class="abs hero-photo" role="img" aria-label="Photo of two smiling businessmen in suits at a desk"></div>
  <span class="abs arrow" style="left:22px">&#8249;</span>
  <span class="abs arrow" style="left:756px;color:#aaa">&#8250;</span>
  <ul class="abs perks">
    <li>Low Rate Car Loans From 4.69%<br>Comparison Rate 4.99%</li>
    <li>Low Fees</li>
    <li>Low Total Cost Loans</li>
  </ul>
  <div class="abs stamp" role="img" aria-label="Low rate guarantee stamp"></div>

  <form class="abs quote">
    <h3>QUICK &amp; EASY QUOTE</h3>
    <div class="field" style="top:48px">First Name</div>
    <div class="field" style="top:77px">Last Name</div>
    <div class="field" style="top:108px">Email Address</div>
    <div class="field" style="top:138px">Phone Number</div>
    <div class="field" style="top:168px">Loan Amount In Dollars<span style="position:absolute;right:8px;top:0">&#8964;</span></div>
    <div class="agree"><span class="box"></span>I Agree To The Terms &amp; Conditions</div>
    <div class="cta">GET MY BEST RATE NOW</div>
  </form>
</section>

<section>
  <h2 class="abs h2" style="left:54px;top:450px"><b>ONLINE LOAN</b> PRE APPROVAL</h2>
  <div class="abs rule" style="left:54px;top:480px;width:288px"></div>
  <p class="abs copy" style="left:54px;top:500px;width:295px">Sed ut perspiciatis unde omnis iste natus error sit voluptatem accusantium dolo remque laudantium, totam rem aperiam, eaque ipsa quae ab illo inventore veritatis et quasi architecto beatae vitae dicta sunt explicabo. Sed ut perspiciatis unde omnis iste natus error sit volu. eaque ipsa quae ab illo inventore veritatis et quasi architecto.</p>
  <p class="abs copy" style="left:54px;top:581px;width:295px;letter-spacing:.3px">Sed ut perspiciatis unde omnis iste natus error sit voluptatem accusantium dolo remque laudantium.</p>
  <div class="abs call">Call Today<b>1300 555 216</b></div>

  <div class="abs vdiv"></div>

  <h2 class="abs h2" style="left:393px;top:450px"><b>WE PROVIDE</b> LOANS FOR</h2>
  <div class="abs rule" style="left:393px;top:480px;width:347px"></div>

  <div class="abs loan" style="left:390px;top:506px">
    <div class="ic"><svg width="18" height="14" viewBox="0 0 18 14"><path fill="#fff" d="M3 5 5 1h8l2 4h1v6h-2v2h-2v-2H6v2H4v-2H2V5zm2 0h8l-1-2H6zM4 8a1 1 0 1 0 0 .1zm10 0a1 1 0 1 0 0 .1z"/></svg></div>
    <h4>VEHICLES</h4>
    <p>Sed ut perspiciatis unde omnis iste natus error sit volupta perspiciatis unde .</p>
  </div>
  <div class="abs loan" style="left:575px;top:506px">
    <div class="ic"><svg width="18" height="16" viewBox="0 0 18 16"><path fill="#fff" d="M5 2h8v5H5zM2 8h14l-2 5H4zM1 14h16v1H1z"/></svg></div>
    <h4>BOAT</h4>
    <p>Sed ut perspiciatis unde omnis iste natus error sit volupta perspiciatis unde .</p>
  </div>
  <div class="abs loan" style="left:390px;top:594px">
    <div class="ic"><svg width="18" height="16" viewBox="0 0 18 16"><path fill="#fff" d="M9 1 1 8h2v7h4v-4h4v4h4V8h2z"/></svg></div>
    <h4>HOME</h4>
    <p>Sed ut perspiciatis unde omnis iste natus error sit volupta perspiciatis unde .</p>
  </div>
  <div class="abs loan" style="left:575px;top:594px">
    <div class="ic"><svg width="16" height="18" viewBox="0 0 16 18"><circle cx="8" cy="5" r="3.5" fill="#fff"/><path fill="#fff" d="M2 17c0-5 2-7 6-7s6 2 6 7z"/></svg></div>
    <h4>PERSONAL</h4>
    <p>Sed ut perspiciatis unde omnis iste natus error sit volupta perspiciatis unde .</p>
  </div>
</section>

<section class="abs band-photo" role="img" aria-label="Blurred photo of people meeting at a table">
  <h2>WHAT WILL MY REPAYMENTS BE?</h2>
  <p>See how much you could borrow with our loan calculator.</p>
  <div class="btn-blue">Loan Calculator</div>
</section>

<section class="abs band-blue">
  <h2>Find out what Guaranteed Approval Actually means</h2>
  <p>See how much you could borrow with our loan calculator.</p>
  <div class="btn-light">Find Out More</div>
</section>

<footer class="abs footer">
  <div class="abs foot-brand"><div class="dot"></div><div class="name">BRIGHTPATH FINANCE</div></div>
  <div class="abs foot-phone">1300 555 216</div>
  <div class="abs foot-div"></div>
  <div class="abs foot-links">Home    /    About Us    /    Loans    /    Insurance    /    Finance Calculator    /    Contact Us</div>

  <div class="abs contact" style="left:237px">
    <div class="ic"><svg width="12" height="16" viewBox="0 0 12 16"><path fill="#fff" d="M6 0a6 6 0 0 0-6 6c0 4.5 6 10 6 10s6-5.5 6-10a6 6 0 0 0-6-6zm0 8.5A2.5 2.5 0 1 1 6 3.5a2.5 2.5 0 0 1 0 5z"/></svg></div>
    <div class="txt">BRIGHTPATH FINANCE<br>48 Example Lane<br>Fernhill QA 4872</div>
  </div>
  <div class="abs cdiv" style="left:405px"></div>
  <div class="abs contact" style="left:423px">
    <div class="ic"><svg width="15" height="15" viewBox="0 0 24 24"><path fill="#fff" d="M6.6 10.8a15 15 0 0 0 6.6 6.6l2.2-2.2c.3-.3.7-.4 1-.2 1.1.4 2.3.6 3.6.6.6 0 1 .4 1 1V20c0 .6-.4 1-1 1A17 17 0 0 1 3 4c0-.6.4-1 1-1h3.5c.6 0 1 .4 1 1 0 1.3.2 2.5.6 3.6.1.3 0 .7-.2 1z"/></svg></div>
    <div class="txt">Call Us<br>1300 555 216</div>
  </div>
  <div class="abs cdiv" style="left:553px"></div>
  <div class="abs contact" style="left:572px">
    <div class="ic"><svg width="17" height="12" viewBox="0 0 17 12"><rect x=".5" y=".5" width="16" height="11" fill="none" stroke="#fff"/><path d="M.5.5 8.5 7l8-6.5" fill="none" stroke="#fff"/></svg></div>
    <div class="txt">Email<br>info@brightpath.example.com</div>
  </div>
  <div class="abs foot-rule"></div>
  <div class="abs copyright">Copyright © 2016 BRIGHTPATH FINANCE. All Rights Reserved.</div>
</footer>
<div class="abs base"></div>

</body>
</html>
```